International Clinical Software Company needs a new business card design

We are looking for a new business card design for our company that has recently expanded into the UK market, making us a multinational company.
After having rebranded our website and produced a new style guide, we are looking for a business card that is creative and attention grabbing, while being consistent with the style and colour scheme used on the new website, www.plumvora.example
We produce care management technology for the aged care market, but the main aspect we aim to communicate is the human element of our software, and the way it assists in providing better care for aged people, and stronger relationships between aged people and the staff that care for them.
Our current business card is a dark green with gold text, which makes the text quite difficult to read, not very aesthetically appealing and the colour scheme looks quite dated.
We would like something fresh and modern, that can still be colourful but doesn't use large blocks of dark colour, and uses the colours within our logo.
Something tying in with the leaves that are used in our logo could work quite nicely, along with the Autumn/Fall colours of soft greens, yellows and reds (also in our existing logo). However also happy to look at fresh, completely out of the box ideas we may not have yet considered.
Target Market(s)
The people that receive this business card work in the aged card or health industry and are either corporate/management level staff or clinical (Registered Nurses, care workers etc.)
Industry/Entity Type
Health Product
Contact Information for Business Card
Company Name - BrindlewayCare
Company locations: United Kingdom, Australia, New Zealand
Staff Details:
Staff name: Derek Mallow
Staff job title: Executive Chairman
Staff email: d.mallow@plumvora.example
Office phone number: 01742 918576
Font styles to use
Other font styles liked:
- Calibri
Requirements
Must have
- Must include the BrindlewayCare brand name in it's current font
- Must include logo (3 leaves in gold circle)
- Must include Business Card Details
Nice to have
- Elements of gold
- White space
- Something autumn themed but not too cliched
Should not have
- No blue - used by a major competitor and we would like to differentiate from them
- Large blocks of dark green colour (the green that appears in our leaves on the logo on our current business card is the background colour and it is far too dark)

```html
<!DOCTYPE html>
<html lang="en">
<head>
<meta charset="utf-8">
<title>BrindlewayCare Business Card</title>
<link rel="stylesheet" href="https://fonts.googleapis.com/css2?family=Carlito:wght@400;700&display=swap">
<style>
  :root {
    --page-bg: #ece8e1;
    --card-white: #ffffff;
    --gold: #a39473;
    --gold-soft: #b3a68a;
    --ink: #3a3a36;
    --leaf-orange: #e7862a;
    --leaf-amber: #f2b23a;
    --leaf-yellow: #f4d96a;
    --leaf-pale: #e9ecb0;
    --leaf-mint: #bfe0c6;
    --shadow: rgba(60, 45, 25, 0.22);
  }
  * { margin: 0; padding: 0; box-sizing: border-box; }
  html, body {
    width: 1200px;
    height: 900px;
    overflow: hidden;
    background: var(--page-bg);
    font-family: "Carlito", "Calibri", Arial, sans-serif;
    color: var(--ink);
  }
  .card-set {
    position: relative;
    width: 1200px;
    height: 900px;
  }
  .card {
    position: absolute;
    width: 580px;
    height: 332px;
    border-radius: 3px;
    box-shadow: 0 10px 26px var(--shadow);
    overflow: hidden;
  }
  .card--front { left: 90px; top: 90px; }
  .card--back { left: 530px; top: 478px; background: var(--card-white); }

  .front-artwork {
    position: absolute;
    inset: 0;
    background:
      radial-gradient(ellipse 45% 55% at 20% 35%, var(--leaf-orange) 0%, rgba(231,134,42,0) 70%),
      radial-gradient(ellipse 40% 50% at 25% 85%, var(--leaf-yellow) 0%, rgba(244,217,106,0) 75%),
      radial-gradient(ellipse 30% 35% at 88% 10%, var(--leaf-orange) 0%, rgba(231,134,42,0) 70%),
      radial-gradient(ellipse 50% 60% at 70% 35%, var(--leaf-mint) 0%, rgba(191,224,198,0) 75%),
      linear-gradient(110deg, var(--leaf-amber) 0%, var(--leaf-yellow) 45%, var(--leaf-pale) 100%);
  }
  .front-name {
    position: absolute;
    right: 34px;
    top: 150px;
    font-size: 52px;
    font-weight: 400;
    color: var(--card-white);
    letter-spacing: 0.5px;
    white-space: nowrap;
  }

  .contact-block {
    position: absolute;
    left: 300px;
    top: 40px;
    font-size: 15px;
    line-height: 1.3;
    white-space: nowrap;
  }
  .contact-name {
    font-size: 20px;
    font-weight: 700;
    color: var(--gold);
  }
  .contact-title { margin-bottom: 18px; }
  .contact-locations { margin-left: 30px; margin-bottom: 18px; }
  .contact-email {
    display: flex;
    align-items: center;
    gap: 6px;
    margin-left: 52px;
  }
  .contact-email svg { width: 11px; height: 11px; fill: var(--gold); flex: none; }

  .brand-mark {
    position: absolute;
    left: 34px;
    bottom: 44px;
    display: flex;
    align-items: center;
    gap: 14px;
  }
  .brand-dot {
    width: 92px;
    height: 92px;
    border-radius: 50%;
    border: 3px solid var(--gold);
  }
  .brand-name {
    font-size: 42px;
    font-weight: 400;
    color: var(--gold);
    white-space: nowrap;
  }
</style>
</head>
<body>
  <main class="card-set">
    <section class="card card--front">
      <div class="front-artwork" role="img" aria-label="Photograph of orange and yellow autumn maple leaves against a soft blurred background"></div>
      <div class="front-name">BrindlewayCare</div>
    </section>

    <section class="card card--back">
      <div class="contact-block">
        <div class="contact-name">Derek Mallow</div>
        <div class="contact-title">Executive Chairman</div>
        <div class="contact-locations">United Kingdom, Australia<br>New Zealand</div>
        <div class="contact-email">
          <svg viewBox="0 0 24 24" aria-hidden="true"><path d="M6.6 10.8c1.4 2.8 3.8 5.1 6.6 6.6l2.2-2.2c.3-.3.7-.4 1-.2 1.1.4 2.3.6 3.6.6.6 0 1 .4 1 1V20c0 .6-.4 1-1 1C10.6 21 3 13.4 3 4c0-.6.4-1 1-1h3.5c.6 0 1 .4 1 1 0 1.3.2 2.5.6 3.6.1.3 0 .7-.2 1l-2.3 2.2z"/></svg>
          <span>d.mallow@plumvora.example</span>
        </div>
      </div>
      <div class="brand-mark">
        <div class="brand-dot"></div>
        <div class="brand-name">BrindlewayCare</div>
      </div>
    </section>
  </main>
</body>
</html>
```